I need a business card design for a new business based in South West Australia.
I specialize in residential window cleaning & general handyman maintenance.

Dale Marsh - 412 SILVER HAWK DETAILING
- Window Cleaning
- House Maintenance

```html
<!DOCTYPE html>
<html lang="en">
<head>
<meta charset="utf-8">
<title>412 Silver Hawk Detailing – Business Card</title>
<link href="https://fonts.googleapis.com/css2?family=Old+Standard+TT:wght@400;700&display=swap" rel="stylesheet">
<style>
  :root {
    --page-bg: #e9e4dc;
    --ink: #1f1d1b;
    --band: rgba(255, 255, 255, 0.72);
    --photo-light: #eef0f2;
    --photo-mid: #d9c2ab;
    --photo-skin: #c99877;
    --wood-light: #d9a06b;
    --wood-mid: #c98850;
    --wood-dark: #a9683a;
    --rule: #3a2a1e;
  }
  * { box-sizing: border-box; margin: 0; padding: 0; }
  html, body {
    width: 1200px; height: 970px; overflow: hidden;
    background: var(--page-bg);
  }
  .canvas {
    position: relative; width: 1200px; height: 970px;
  }
  .card {
    position: absolute; left: 50px; top: 156px;
    width: 1100px; height: 658px; overflow: hidden;
    font-family: "Old Standard TT", Georgia, serif;
    color: var(--ink);
    box-shadow: 0 10px 30px rgba(0,0,0,0.18);
  }
  .tools-photo {
    position: absolute; left: 0; top: 0; width: 1100px; height: 444px;
    background:
      linear-gradient(180deg, var(--photo-light) 0%, #e6ddd3 55%, var(--photo-mid) 75%, var(--photo-skin) 100%);
  }
  .title-band {
    position: absolute; left: 0; top: 66px; width: 1100px; height: 264px;
    background: var(--band);
  }
  .company-name {
    position: absolute; left: 0; top: 120px; width: 1100px;
    text-align: center; font-weight: 700; font-size: 54px; letter-spacing: 0.5px;
  }
  .services-line {
    position: absolute; left: 0; top: 222px; width: 1100px;
    text-align: center; font-weight: 700; font-size: 29px; line-height: 44px;
  }
  .name-plank {
    position: absolute; left: 0; top: 444px; width: 1100px; height: 126px;
    background: linear-gradient(90deg, var(--wood-light), var(--wood-mid) 45%, var(--wood-light) 70%, var(--wood-mid));
    border-bottom: 2px solid var(--rule);
  }
  .owner-name {
    position: absolute; left: 0; top: 478px; width: 1100px;
    text-align: center; font-weight: 700; font-size: 56px;
  }
  .service-plank {
    position: absolute; left: 0; top: 570px; width: 1100px; height: 88px;
    background: linear-gradient(90deg, var(--wood-mid), var(--wood-light) 40%, var(--wood-dark) 100%);
  }
  .service {
    position: absolute; top: 592px; font-weight: 700; font-size: 35px;
    display: flex; align-items: center; gap: 10px;
  }
  .service-left { left: 60px; }
  .service-right { right: 28px; }
  .service svg { width: 28px; height: 28px; }
</style>
</head>
<body>
<div class="canvas">
  <div class="card">
    <div class="tools-photo" role="img" aria-label="Photo of many raised hands holding tools: drills, tape measures, spirit levels, wrenches and a set square"></div>
    <div class="title-band"></div>
    <h1 class="company-name">412 SILVER HAWK DETAILING</h1>
    <p class="services-line">residential window cleaning &amp;<br>general handyman maintenance</p>
    <div class="name-plank" role="img" aria-label="Light pine wood plank texture"></div>
    <h2 class="owner-name">Dale Marsh</h2>
    <div class="service-plank" role="img" aria-label="Light pine wood plank texture"></div>
    <p class="service service-left">Window Cleaning</p>
    <p class="service service-right">House Maintenance
      <svg viewBox="0 0 28 28" aria-hidden="true">
        <circle cx="14" cy="14" r="10" fill="none" stroke="#1f1d1b" stroke-width="2.5"/>
        <circle cx="14" cy="14" r="4" fill="#1f1d1b"/>
        <path d="M14 1v6M14 21v6M1 14h6M21 14h6" stroke="#1f1d1b" stroke-width="2.5"/>
      </svg>
    </p>
  </div>
</div>
</body>
</html>
```